Dynamic Business Card for Sports Supplements Company

Hi! I'm looking for an awesome business card to match my existing sports supplement company. I have uploaded my current company logo and screenshot of the front page of my website.

I would like to have something dynamic and interesting and utilize the colors in the website - the reds and purples

The business card should be double sided and focus on a unique eye-catching design on the back and include all the relevant company info.

Most importantly, it should say somewhere: "Sign up on our website for a coupon code."

Target Market(s)

Mostly for women gym goers but it shouldn't be too feminine. It should be in keeping with the website design. It should flow and clearly be connected to it

Industry/Entity Type

Business

Contact Information for Business Card

Lorraine K. Vestal
CEO
LVestal@Quorvanexco.com
www.quorvanexco.com
555.417.3820
P.O. Box 47315
Fernbrook, Calder 00000

Sign up on our website for a coupon code

Font styles to use
Serif
Sans Serif
Other font styles liked:
• Novecento font family and "Quorvanex" is in AR Destine font

Requirements
Must have
• One side should be a bold Quorvanex logo design. Even just the symbol itself may be o.k. (see attached file)

```html
<!DOCTYPE html>
<html lang="en">
<head>
<meta charset="utf-8">
<title>Quorvanex Business Card</title>
<link href="https://fonts.googleapis.com/css2?family=Open+Sans:wght@400;600;700&display=swap" rel="stylesheet">
<style>
  :root {
    --page-bg: #e9e6e1;
    --slate-dark: #2a2b2c;
    --slate-mid: #3d3f40;
    --slate-light: #4a4c4d;
    --brand-red: #e3232a;
    --ink: #262626;
    --paper: #ffffff;
    --chalk: #f4f4f4;
  }
  html, body {
    margin: 0;
    padding: 0;
    width: 1200px;
    height: 902px;
    overflow: hidden;
    background: var(--page-bg);
    font-family: "Open Sans", Arial, sans-serif;
  }
  .business-card {
    position: absolute;
    left: 100px;
    top: 165px;
    width: 1000px;
    height: 571px;
    border-radius: 22px;
    overflow: hidden;
    background: var(--paper);
    box-shadow: 0 12px 30px rgba(0,0,0,0.18);
  }
  .card-shapes {
    position: absolute;
    inset: 0;
    width: 1000px;
    height: 571px;
  }
  .contact-side {
    position: absolute;
    left: 52px;
    top: 0;
    width: 480px;
    height: 571px;
    color: var(--chalk);
  }
  .holder-name {
    position: absolute;
    top: 62px;
    margin: 0;
    font-size: 34px;
    font-weight: 700;
    line-height: 1.2;
    color: var(--chalk);
    white-space: nowrap;
  }
  .holder-title {
    position: absolute;
    top: 104px;
    margin: 0;
    font-size: 25px;
    font-weight: 400;
    color: var(--brand-red);
  }
  .postal-address {
    position: absolute;
    top: 227px;
    margin: 0;
    font-style: normal;
    font-size: 25px;
    line-height: 34px;
    white-space: nowrap;
  }
  .contact-list {
    position: absolute;
    top: 331px;
    margin: 0;
    padding: 0;
    list-style: none;
    font-size: 25px;
    line-height: 34px;
    white-space: nowrap;
  }
  .contact-item {
    display: flex;
    align-items: center;
    gap: 10px;
  }
  .contact-icon {
    width: 27px;
    height: 27px;
    flex: none;
  }
  .coupon-note {
    position: absolute;
    top: 447px;
    margin: 0;
    font-size: 25px;
    line-height: 34px;
    white-space: nowrap;
  }
  .coupon-note .highlight {
    color: var(--brand-red);
    font-weight: 600;
  }
  .brand-side {
    position: absolute;
    left: 540px;
    top: 0;
    width: 420px;
    height: 531px;
    padding-bottom: 40px;
    display: flex;
    align-items: center;
    justify-content: center;
    gap: 14px;
  }
  .brand-mark {
    width: 36px;
    height: 36px;
    background: var(--brand-red);
  }
  .brand-name {
    font-family: "Open Sans", Arial, sans-serif;
    font-size: 58px;
    font-weight: 700;
    color: var(--ink);
    letter-spacing: 1px;
  }
</style>
</head>
<body>
  <div class="business-card">
    <svg class="card-shapes" viewBox="0 0 1000 571" xmlns="http://www.w3.org/2000/svg">
      <defs>
        <radialGradient id="slate-texture" cx="40%" cy="35%" r="80%">
          <stop offset="0%" stop-color="#4a4c4d"/>
          <stop offset="55%" stop-color="#3d3f40"/>
          <stop offset="100%" stop-color="#2a2b2c"/>
        </radialGradient>
      </defs>
      <path class="slate-panel" role="img" aria-label="Dark chalkboard texture background"
            d="M0 0 H545 Q413 285.5 545 571 H0 Z" fill="url(#slate-texture)"/>
      <path class="accent-curve" d="M553 0 Q426 285.5 553 571 L560 571 Q444 285.5 560 0 Z" fill="#e3232a"/>
      <circle class="edge-dot" cx="0" cy="100" r="27" fill="#e3232a"/>
    </svg>

    <section class="contact-side">
      <h1 class="holder-name">Lorraine K. Vestal</h1>
      <p class="holder-title">CEO</p>

      <address class="postal-address">
        P.O. Box 47315<br>
        Fernbrook, Calder 00000
      </address>

      <ul class="contact-list">
        <li class="contact-item">
          <svg class="contact-icon" viewBox="0 0 27 27" aria-hidden="true">
            <rect width="27" height="27" rx="5" fill="#e3232a"/>
            <path d="M6 11 Q13.5 5 21 11 L19 13 L17 11.5 L10 11.5 L8 13 Z" fill="#2a2b2c"/>
            <rect x="8" y="13.5" width="11" height="7" rx="1.5" fill="#2a2b2c"/>
          </svg>
          <span>555.417.3820</span>
        </li>
        <li class="contact-item">
          <svg class="contact-icon" viewBox="0 0 27 27" aria-hidden="true">
            <rect width="27" height="27" rx="5" fill="#e3232a"/>
            <rect x="5.5" y="8" width="16" height="11" fill="none" stroke="#2a2b2c" stroke-width="1.8"/>
            <path d="M5.5 8 L13.5 14.5 L21.5 8" fill="none" stroke="#2a2b2c" stroke-width="1.8"/>
          </svg>
          <span>LVestal@Quorvanexco.com</span>
        </li>
        <li class="contact-item">
          <svg class="contact-icon" viewBox="0 0 27 27" aria-hidden="true">
            <rect width="27" height="27" rx="5" fill="#e3232a"/>
            <circle cx="13.5" cy="13.5" r="7.5" fill="none" stroke="#2a2b2c" stroke-width="1.6"/>
            <ellipse cx="13.5" cy="13.5" rx="3.5" ry="7.5" fill="none" stroke="#2a2b2c" stroke-width="1.4"/>
            <path d="M6 13.5 H21 M7.5 10 H19.5 M7.5 17 H19.5" stroke="#2a2b2c" stroke-width="1.2"/>
          </svg>
          <span>www.quorvanexco.com</span>
        </li>
      </ul>

      <p class="coupon-note">
        <span class="highlight">Sign up</span> on<br>
        our website for a coupon code
      </p>
    </section>

    <section class="brand-side">
      <span class="brand-mark"></span>
      <span class="brand-name">Quorvanex</span>
    </section>
  </div>
</body>
</html>
```